Tallow Crest - Facebook Cover Photo & Photo Icon Design

We’re looking for a Facebook Cover Photo and Profile Icon design for Tallow Crest, a leading Residential Real Estate brand under Kestmore Property Agents, based in Capalaba and Alexandra Hills, Queensland, Australia.

This design will represent my professional real estate profile and needs to be bold, clean, and on-brand.

Deliverables:

Facebook Cover Photo (820 x 312 px, optimized for mobile + desktop)

Facebook Profile Icon (1:1 ratio, minimum 320 x 320 px)

Design Guidelines:

1. Must Include:

The Tallow Crest logo (provided after project start)

Use of the Kestmore Property Agents brand colour palette (will be supplied)

Clear connection to residential real estate

2. Optional but Preferred:

A local photo or skyline of Capalaba or Alexandra Hills in QLD (bonus points for this)

Space for a short tagline like:
“Selling Faster. Selling Smarter. Selling Kestmore.”
(Optional tagline – open to variations if it improves layout/design)

3. Style & Feel:

Professional yet personable

Clean, modern aesthetic

Subtle touches of fun or personality are welcome

Layout must work well when overlaid by Facebook UI elements (like profile photo & call-to-action buttons)

Who I Am:
I'm a well-known residential real estate agent in the Redlands area, known for high-energy campaigns, premium video marketing, and a results-driven approach. My brand is fun, fresh, and high-performing — just like the real estate campaigns I run.

Files to be Provided (after selection):

Tallow Crest logo in high-res

Brand colour palette / style reference

Optional photo references if local imagery is not sourced by designer

Final Notes:

Make sure all text is legible on mobile and desktop

Original, layered design files must be delivered (PSD or AI preferred)

Bonus points if it feels uniquely “Bayside Queensland” while maintaining a national-level professional polish

Target Market(s)

Alexandra Hills, Capalaba & Sheldon

Industry/Entity Type

Real Estate

Colors
0054AA
0677BA
7BADD7
CADEEF
E8F1F8

Requirements
Must have
• Headshot, Mobile Number 0417 962 085, Suburbs - Alexandra Hills, Capalaba & Sheldon
Nice to have
• White, Crisp & Professional. Bottom Banner with Suburb List. Specialising in Alexandra Hills, Capalaba & Sheldon

```html
<!DOCTYPE html>
<html lang="en">
<head>
<meta charset="utf-8">
<title>Tallow Crest – Facebook Cover &amp; Profile Icon</title>
<link rel="stylesheet" href="https://fonts.googleapis.com/css2?family=Montserrat:wght@300;400;500;600&display=swap">
<style>
  :root {
    --navy: #0b176a;
    --navy-deep: #0a1250;
    --night: #10163a;
    --gold: #d6a964;
    --white: #ffffff;
    --page: #ffffff;
  }
  * { margin: 0; padding: 0; box-sizing: border-box; }
  html, body { width: 1200px; height: 1159px; overflow: hidden; background: var(--page); }
  body { position: relative; font-family: "Montserrat", sans-serif; }

  .cover {
    position: absolute; left: 55px; top: 423px;
    width: 820px; height: 312px; overflow: hidden;
    background: var(--white);
    box-shadow: 0 4px 14px rgba(0,0,0,0.18);
  }
  .cover-art { position: absolute; inset: 0; }

  .tagline {
    position: absolute; left: 26px; top: 18px;
    font-size: 37px; line-height: 46px; text-transform: uppercase;
    color: var(--white); font-weight: 600; white-space: nowrap;
  }
  .tagline .accent { color: var(--gold); font-weight: 300; }

  .brand-name {
    position: absolute; left: 597px; top: 24px; width: 200px;
    text-align: center; color: var(--navy);
    font-size: 36px; line-height: 38px; font-weight: 400; letter-spacing: 2px;
  }

  .phone {
    position: absolute; right: 240px; top: 223px;
    font-size: 23px; font-weight: 500; color: var(--navy); white-space: nowrap;
  }
  .suburbs {
    position: absolute; right: 240px; top: 256px;
    font-size: 14px; line-height: 18px; font-weight: 500; color: var(--navy);
    text-align: right; white-space: nowrap;
  }

  .profile-icon {
    position: absolute; left: 915px; top: 464px;
    width: 230px; height: 230px; overflow: hidden;
    background: var(--navy);
    box-shadow: 0 4px 14px rgba(0,0,0,0.18);
  }
  .profile-icon svg { position: absolute; inset: 0; }
  .profile-icon .brand-name {
    left: 0; top: 80px; width: 230px; color: var(--white);
    font-size: 30px; line-height: 34px;
  }
</style>
</head>
<body>

<section class="cover" aria-label="Facebook cover photo">
  <svg class="cover-art" width="820" height="312" viewBox="0 0 820 312">
    <defs>
      <linearGradient id="nightPhoto" x1="0" y1="0" x2="1" y2="1">
        <stop offset="0" stop-color="#26337a"/>
        <stop offset="0.55" stop-color="#141b45"/>
        <stop offset="1" stop-color="#3a3026"/>
      </linearGradient>
      <linearGradient id="fadeWhite" x1="0" y1="0" x2="1" y2="0">
        <stop offset="0" stop-color="#ffffff" stop-opacity="0"/>
        <stop offset="1" stop-color="#ffffff" stop-opacity="1"/>
      </linearGradient>
      <linearGradient id="houseTone" x1="0" y1="0" x2="0" y2="1">
        <stop offset="0" stop-color="#e9e9e9"/>
        <stop offset="0.6" stop-color="#8f8a82"/>
        <stop offset="1" stop-color="#3b3a38"/>
      </linearGradient>
      <linearGradient id="agentTone" x1="0" y1="0" x2="0" y2="1">
        <stop offset="0" stop-color="#c9a48c"/>
        <stop offset="0.35" stop-color="#3c4a6b"/>
        <stop offset="1" stop-color="#26324f"/>
      </linearGradient>
    </defs>

    <g role="img" aria-label="Evening photograph of a modern two-storey home with lit windows and landscaped garden">
      <polygon points="0,0 622,0 470,312 0,312" fill="url(#nightPhoto)"/>
    </g>
    <rect class="photo-fade" x="330" y="200" width="200" height="112" fill="url(#fadeWhite)"/>

    <rect class="gold-band" x="466" y="0" width="100" height="170" fill="var(--gold)"/>
    <polygon class="gold-corner" points="820,107 820,312 606,312" fill="var(--gold)"/>

    <circle class="navy-disc" cx="756" cy="192" r="44" fill="var(--navy)"/>
    <circle class="navy-dot" cx="796" cy="212" r="6" fill="var(--navy)"/>

    <path class="agent-headshot" role="img" aria-label="Headshot of the agent in a navy blazer and white shirt"
          d="M636 312 C 640 250, 660 228, 690 218 C 678 200, 672 160, 712 150 C 752 160, 748 200, 736 218 C 766 228, 790 250, 794 312 Z"
          fill="url(#agentTone)"/>

    <g role="img" aria-label="Illustration of a modern glass-fronted three-level house">
      <polygon points="432,118 498,66 596,100 604,190 442,196" fill="url(#houseTone)"/>
    </g>

    <path class="gold-wave" d="M-4 198 C 40 180, 100 172, 170 184 S 300 214, 360 206 S 440 190, 468 160"
          fill="none" stroke="var(--gold)" stroke-width="12" stroke-linecap="round"/>

    <g class="phone-icon" fill="var(--gold)">
      <path d="M593 227 c2-2 4-2 5 0 l3 4 c1 1 1 3-1 4 l-2 1 c1 3 4 6 7 7 l1-2 c1-2 3-2 4-1 l4 3 c2 1 2 3 0 5 l-2 2 c-3 2-9 0-14-5 s-8-12-5-15 z"/>
    </g>
    <line class="rule" x1="586" y1="256" x2="616" y2="256" stroke="var(--gold)" stroke-width="1.5"/>
    <g class="suburb-icon" fill="var(--gold)">
      <polygon points="588,272 595,265 602,272 602,280 588,280"/>
      <rect x="606" y="264" width="3" height="10" rx="1.5"/>
      <rect x="612" y="266" width="3" height="9" rx="1.5"/>
      <rect x="591" y="284" width="3" height="10" rx="1.5"/>
      <polygon points="600,292 607,285 614,292 614,298 600,298"/>
    </g>
  </svg>

  <h1 class="tagline">
    <span>Selling Faster.</span><br>
    <span class="accent">Selling Smarter.</span><br>
    <span>Selling Kestmore.</span>
  </h1>

  <p class="brand-name">TALLOW<br>CREST</p>

  <p class="phone">0417 962 085</p>
  <p class="suburbs">Specialising in Alexandra Hills,<br>Capalaba &amp; Sheldon</p>
</section>

<section class="profile-icon" aria-label="Facebook profile icon">
  <svg width="230" height="230" viewBox="0 0 230 230">
    <defs>
      <linearGradient id="iconPhoto" x1="0" y1="0" x2="0" y2="1">
        <stop offset="0" stop-color="#2a3a8a" stop-opacity="0"/>
        <stop offset="1" stop-color="#2a3a8a" stop-opacity="0.55"/>
      </linearGradient>
    </defs>
    <rect role="img" aria-label="Faint photograph of a modern building" x="0" y="140" width="230" height="90" fill="url(#iconPhoto)"/>
    <path class="gold-wave" d="M-4 56 C 40 28, 90 42, 130 58 S 200 62, 234 32"
          fill="none" stroke="var(--gold)" stroke-width="9" stroke-linecap="round"/>
  </svg>
  <p class="brand-name">TALLOW<br>CREST</p>
</section>

</body>
</html>
```